Oakmere Animal Care Group of Central Pennsylvania

I need a business card design for a new company in Harrisburg PA called "Animal Care Oakmere Group of Central PA". I will be providing relief services for veterinarians who need coverage during vacations; sick/maternity leave, etc. I would like to see the veterinarian symbol incorporated in the design in combination with animals (dogs /cats/birds/reptiles an pocket pets). Include My full name: Tomás R. Quintaval DVM, MLAS, BS. Also include my e mail (dvmtrq@mailbrook.net) and phone number 5552846017

Target Market(s)

Small Animal Veterinarian, practice owner

Industry/Entity Type

Business

Contact Information for Business Card

Oakmere Animal Care Group of Central PA

Font styles to use
Script

Requirements
Must have
• Veterinarian caduceus (see image) and Small animals (pets) within the logo.
Nice to have
• Give a sense of relaxation (vacationing)
Should not have
• Large animals, i.e. horses, cows, zoo animals...

```html
<!DOCTYPE html>
<html lang="en">
<head>
<meta charset="utf-8">
<title>Oakmere Animal Care Group – Business Card</title>
<link rel="stylesheet" href="https://fonts.googleapis.com/css2?family=Great+Vibes&family=Cinzel:wght@600&family=Arimo:wght@400&display=swap">
<style>
  :root {
    --bg: #e9e6e1;
    --card-white: #ffffff;
    --brand-red: #c1272d;
    --brand-red-dark: #a61e24;
    --ink: #1d1d1d;
    --swoosh-black: #222222;
    --on-red: #ffffff;
  }
  * { margin: 0; padding: 0; box-sizing: border-box; }
  html, body {
    width: 1200px; height: 818px; overflow: hidden;
    background: var(--bg);
  }
  .card {
    position: absolute; left: 100px; top: 123px;
    width: 1000px; height: 572px;
    background: var(--card-white);
    box-shadow: 0 10px 30px rgba(0,0,0,0.18);
    overflow: hidden;
  }
  .card-shapes { position: absolute; inset: 0; }
  .brand-mark {
    position: absolute; left: 88px; top: 175px;
    width: 110px; height: 110px; border-radius: 50%;
    border: 6px solid var(--brand-red);
  }
  .brand-name {
    position: absolute; left: 70px; top: 310px; width: 380px;
    font-family: "Cinzel", serif; font-weight: 600;
    color: var(--ink); font-size: 28px; line-height: 1.25;
    letter-spacing: 0.5px;
  }
  .person {
    position: absolute; left: 110px; top: 34px;
    display: flex; flex-direction: column; align-items: flex-end;
  }
  .person-name {
    font-family: "Great Vibes", cursive;
    font-size: 52px; color: var(--ink); line-height: 1.1;
    white-space: nowrap;
  }
  .person-title {
    font-family: "Arimo", sans-serif;
    font-size: 20px; color: var(--brand-red);
    margin-top: 2px; white-space: nowrap;
  }
  .contact {
    position: absolute; right: 44px; top: 190px;
    font-family: "Arimo", sans-serif; color: var(--on-red);
    font-size: 26px; text-align: right;
  }
  .contact-line {
    display: flex; align-items: center; justify-content: flex-end;
    gap: 14px; margin-bottom: 14px;
  }
  .contact-icon { width: 26px; height: 26px; flex: none; }
</style>
</head>
<body>
  <div class="card">
    <svg class="card-shapes" viewBox="0 0 1000 572" width="1000" height="572" aria-hidden="true">
      <path class="red-band" fill="var(--brand-red)"
        d="M610 0 C540 110 540 250 480 350 C440 430 390 510 350 572 L1000 572 L1000 0 Z"/>
      <path class="white-stripe" fill="var(--card-white)"
        d="M660 0 C600 90 585 200 540 300 C505 380 470 440 430 480 C490 430 530 370 560 300 C605 200 620 100 680 0 Z"/>
      <path class="black-swoosh" fill="var(--swoosh-black)"
        d="M465 240 C470 380 410 490 290 572 L318 572 C440 490 480 380 465 240 Z"/>
      <path class="red-swoosh" fill="var(--brand-red-dark)"
        d="M505 200 C510 360 450 480 330 572 L342 572 C470 480 515 360 505 200 Z"/>
    </svg>

    <div class="brand-mark"></div>
    <div class="brand-name">Animal Care Oakmere<br>Group of Central PA</div>

    <div class="person">
      <div class="person-name">Tomás R. Quintaval</div>
      <div class="person-title">Managing Director</div>
    </div>

    <div class="contact">
      <div class="contact-line">
        <span>5552846017</span>
        <svg class="contact-icon" viewBox="0 0 24 24" aria-label="Phone">
          <path fill="var(--on-red)" d="M6.6 10.8c1.4 2.8 3.8 5.1 6.6 6.6l2.2-2.2c.3-.3.7-.4 1-.2 1.1.4 2.3.6 3.6.6.6 0 1 .4 1 1V20c0 .6-.4 1-1 1C10.6 21 3 13.4 3 4c0-.6.4-1 1-1h3.5c.6 0 1 .4 1 1 0 1.3.2 2.5.6 3.6.1.3 0 .7-.2 1L6.6 10.8z"/>
        </svg>
      </div>
      <div class="contact-line">
        <span>dvmtrq@mailbrook.net</span>
        <svg class="contact-icon" viewBox="0 0 24 24" aria-label="Email">
          <rect x="2" y="5" width="20" height="14" fill="var(--on-red)"/>
          <path d="M2 5 L12 13 L22 5" fill="none" stroke="var(--brand-red)" stroke-width="1.6"/>
        </svg>
      </div>
    </div>
  </div>
</body>
</html>
```